Brackwell Exteriors Needs a New Website!

We are an exteriors company specializing in vinyl siding, Corwin Maddox siding, aluminum soffit/fascia, trough. We do new construction work as well as renovations. We also build detached garages.
You can view our current website at www.brackwellfabricators.ca
I want to completely overhaul the website.
Our services are different now as we no longer do new home construction as well as we do not do the snow clearing.
I want to focus on 2 things in particular on the website:

1/ Exterior renovations

2/ Detached Garage construction.

I have included our logo in the attached files to use as well.

Some features we would like:

1/ Be able to easily attach a video from Clipverse/Reelio to highlight a product or service
2/ Quick chat or contact button that we can talk to a potential client quickly
3/ Meet the Team page that is interesting and fresh
4/ Place for us to put in helpful exterior tips/suggestions for homeowners.

Content is not important, but looking for the best design that will attract people once they click on our page and want to renovate with us.

Target Market(s)

People looking for renovations on their home, people looking to build a detached garage.

Industry/Entity Type

Residential Construction

Number of Pages Required

5+ page

Font styles to use
Sans Serif

Requirements
Must have
• Fresh and exciting home page.

Simple design. Don't want it over complicated or too much information to confuse the potential client.

Easy way to contact us.

Meet the team page that instills confidence
Nice to have
• Colour of website to go off our logo. Doesn't need to be an exact match, but something that goes well with our blue and grey.

```html
<!DOCTYPE html>
<html lang="en">
<head>
<meta charset="utf-8">
<title>Brackwell Exteriors – Contact Us</title>
<link href="https://fonts.googleapis.com/css2?family=Montserrat:wght@400;500;600;700;800&display=swap" rel="stylesheet">
<style>
:root{
  --blue:#0a6fc0;
  --blue-deep:#0668b8;
  --blue-soft:#ddeff9;
  --blue-ring:#c3def2;
  --page:#f4f9fd;
  --ink:#111418;
  --text:#2b2f35;
  --muted:#6a7078;
  --white:#ffffff;
  --night:#0c0d10;
}
*{box-sizing:border-box;margin:0;padding:0}
html,body{width:707px;height:1200px;overflow:hidden}
body{position:relative;background:var(--page);font-family:"Montserrat",sans-serif;color:var(--text)}
.abs{position:absolute}

/* hero */
.hero{left:0;top:0;width:707px;height:355px;
  background:linear-gradient(100deg,#1b2736 0%,#3a4a5e 25%,#1a2433 48%,#2a3546 70%,#4d5a6d 100%);
  clip-path:polygon(0 0,100% 0,100% 65%,0 100%)}
.hero-shade{left:0;top:0;width:707px;height:355px;
  background:linear-gradient(180deg,rgba(255,255,255,.25) 0%,rgba(0,0,0,0) 25%,rgba(0,0,0,.55) 100%);
  clip-path:polygon(0 0,100% 0,100% 65%,0 100%)}

.brand{display:flex;align-items:center;gap:5px;color:var(--blue);font-weight:700;letter-spacing:.3px}
.brand-dot{border-radius:50%;border:3px solid currentColor}
.brand-top{left:95px;top:15px;font-size:12px}
.brand-top .brand-dot{width:22px;height:22px}

.nav{top:23px;display:flex;font-size:7.5px;font-weight:500;color:var(--ink)}
.nav a{position:absolute;white-space:nowrap;color:var(--ink);text-decoration:none}
.nav .active{color:var(--blue);font-weight:700}
.nav-rule{left:95px;top:53px;width:521px;height:1px;background:rgba(255,255,255,.45)}
.nav-mark{left:555px;top:52px;width:61px;height:2px;background:var(--blue)}

.hero-title{left:96px;top:158px;font-size:25px;font-weight:800;color:var(--white);letter-spacing:.5px}
.crumb{left:96px;top:192px;font-size:7.5px;color:var(--white);font-weight:500}

/* contact section */
.sec-title{left:0;width:707px;text-align:center;font-size:16.5px;font-weight:800;color:var(--ink);letter-spacing:.6px}
.sec-title span{color:var(--blue)}
.sec-line{left:336px;width:35px;height:1.5px;background:var(--blue)}
.lead{left:0;width:707px;top:382px;text-align:center;font-size:8px}

.card{top:423px;width:159px;height:110px;background:var(--blue-soft);border-radius:8px;text-align:center}
.badge{top:407px;width:54px;height:54px;border-radius:50%;background:var(--blue-ring);display:flex;align-items:center;justify-content:center}
.badge i{width:43px;height:43px;border-radius:50%;background:var(--blue);display:flex;align-items:center;justify-content:center}
.card h3{position:absolute;left:0;right:0;top:55px;font-size:8px;font-weight:700;color:var(--ink);letter-spacing:.3px}
.card p{position:absolute;left:8px;right:8px;top:70px;font-size:7.3px;line-height:12px;color:var(--text)}

/* blue band */
.band{left:0;top:700px}

/* form */
.panel-back2{left:102px;top:870px;width:501px;height:22px;background:#5aa2d9;border-radius:0 0 6px 6px}
.panel-back1{left:98px;top:865px;width:509px;height:20px;background:#b8daf2;border-radius:0 0 6px 6px}
.panel{left:94px;top:578px;width:517px;height:298px;background:var(--blue-soft);border-radius:6px}
.field{background:var(--white);border:1px solid #c9d3dc;font-size:6.5px;color:var(--muted);padding:0 9px;display:flex;align-items:center}
.field.area{align-items:flex-start;padding-top:9px}
.chev{position:absolute;right:12px;top:11px}
.captcha{left:274px;top:780px;width:157px;height:26px;background:#f9f9f9;border:1px solid #d3d3d3;border-radius:2px;font-size:6px;color:#222}
.captcha .box{position:absolute;left:5px;top:7px;width:12px;height:12px;border:1.5px solid #c1c1c1;border-radius:2px;background:var(--white)}
.captcha .lbl{position:absolute;left:21px;top:9px}
.captcha .gate{position:absolute;right:5px;top:5px;text-align:center;font-size:3.3px;color:#777;line-height:5px}
.captcha .gate b{display:block;margin:0 auto 1px;width:9px;height:9px;border-radius:50%;border:2px solid #4a90e2}
.submit{left:318px;top:816px;width:72px;height:22px;background:var(--blue-deep);color:var(--white);font-size:7.5px;font-weight:700;display:flex;align-items:center;justify-content:center;box-shadow:0 2px 4px rgba(0,0,0,.2);border-radius:1px}

.chat{left:655px;top:692px;width:38px;height:38px;border-radius:50%;background:var(--white);display:flex;align-items:center;justify-content:center;box-shadow:0 2px 8px rgba(0,0,0,.12)}

/* footer */
.brand-foot{left:0;width:707px;top:953px;justify-content:center;color:var(--white);font-size:19px}
.brand-foot .brand-dot{width:42px;height:42px;border-width:4px}
.foot-nav{top:1027px;left:0;width:707px;display:flex;justify-content:center;font-size:8.5px;font-weight:500;color:var(--white)}
.foot-nav span{padding:0 16px;border-right:1px solid rgba(255,255,255,.35);line-height:8px}
.foot-nav span:last-child{border-right:0}
.fcol{top:1070px;text-align:center;color:var(--white)}
.fcol svg{display:block;margin:0 auto}
.fcol h4{margin-top:9px;font-size:8.5px;font-weight:700;letter-spacing:.3px}
.fcol p{margin-top:4px;font-size:7.3px;line-height:12px}

.bottom{left:0;top:1167px;width:707px;height:33px;background:var(--night)}
.copy{left:95px;top:1178px;font-size:7.3px;color:var(--white)}
.social{top:1174px;width:18px;height:18px;border-radius:50%;background:var(--blue);border:1px solid rgba(255,255,255,.7)}
</style>
</head>
<body>

<div class="abs hero" role="img" aria-label="Photo of a businessman in a suit holding a smartphone, with glowing phone, mail and at-sign contact icons floating above a blurred city background"></div>
<div class="abs hero-shade"></div>

<div class="abs brand brand-top"><span class="brand-dot"></span>BRACKWELL EXTERIORS</div>
<nav class="abs nav">
  <a style="left:293px">HOME</a>
  <a style="left:342px">ABOUT US</a>
  <a style="left:407px">SERVICES</a>
  <a style="left:470px">MEET THE TEAM</a>
  <a class="active" style="left:560px">CONTACT US</a>
</nav>
<div class="abs nav-rule"></div>
<div class="abs nav-mark"></div>

<h1 class="abs hero-title">CONTACT US</h1>
<div class="abs crumb">HOME - CONTACT US</div>

<h2 class="abs sec-title" style="top:344px">CONTACT <span>US</span></h2>
<div class="abs sec-line" style="top:369px"></div>
<p class="abs lead">Rather pick up the phone and call us directly? See the direct contact information below.</p>

<div class="abs card" style="left:95px"><h3>PHONE</h3><p>+1 780-555-0184</p></div>
<div class="abs card" style="left:274px"><h3>BRACKWELL EXTERIORS</h3><p>48210 Harlow Rd 118 #305, Elmford<br>Park, AB T9C 2M4, Canada</p></div>
<div class="abs card" style="left:452px"><h3>EMAIL</h3><p>hello@brackwellexteriors.ca</p></div>

<div class="abs badge" style="left:147px"><i><svg width="18" height="18" viewBox="0 0 24 24"><path fill="#fff" d="M6.6 10.8a15.1 15.1 0 006.6 6.6l2.2-2.2a1 1 0 011-.25 11.4 11.4 0 003.6.57 1 1 0 011 1V20a1 1 0 01-1 1A17 17 0 013 4a1 1 0 011-1h3.5a1 1 0 011 1c0 1.25.2 2.45.57 3.57a1 1 0 01-.25 1z"/></svg></i></div>
<div class="abs badge" style="left:326px"><i><svg width="16" height="18" viewBox="0 0 24 24"><path fill="#fff" d="M12 2a7 7 0 00-7 7c0 5.25 7 13 7 13s7-7.75 7-13a7 7 0 00-7-7zm0 9.5A2.5 2.5 0 1112 6.5a2.5 2.5 0 010 5z"/></svg></i></div>
<div class="abs badge" style="left:505px"><i><svg width="18" height="14" viewBox="0 0 24 18"><path fill="#fff" d="M2 0h20a2 2 0 012 2v.6l-12 7.5L0 2.6V2a2 2 0 012-2zM0 5l12 7.5L24 5v11a2 2 0 01-2 2H2a2 2 0 01-2-2z"/></svg></i></div>

<svg class="abs band" width="707" height="467" viewBox="0 0 707 467" aria-hidden="true">
  <polygon points="0,130 707,15 707,467 0,467" fill="#0a72c2"/>
  <polygon points="0,215 707,110 707,170 0,300" fill="#1179c6" opacity=".7"/>
  <polygon points="0,385 707,250 707,300 0,450" fill="#1780ca" opacity=".5"/>
</svg>

<div class="abs panel-back2"></div>
<div class="abs panel-back1"></div>
<div class="abs panel"></div>
<h2 class="abs sec-title" style="top:609px">QUICK <span>INQUIRY</span></h2>
<div class="abs sec-line" style="top:633px"></div>

<div class="abs field" style="left:121px;top:651px;width:225px;height:25px">Name*</div>
<div class="abs field" style="left:359px;top:651px;width:225px;height:25px">Phone*</div>
<div class="abs field" style="left:121px;top:684px;width:225px;height:25px">Email*</div>
<div class="abs field" style="left:359px;top:684px;width:225px;height:25px">Choose a Service
  <svg class="chev" width="6" height="4" viewBox="0 0 6 4"><path d="M.5.5L3 3 5.5.5" fill="none" stroke="#333" stroke-width="1"/></svg></div>
<div class="abs field area" style="left:121px;top:717px;width:463px;height:57px">Message*</div>

<div class="abs captcha">
  <span class="box"></span><span class="lbl">I'm not a robot</span>
  <span class="gate"><b></b>CheckGate<br>Privacy · Terms</span>
</div>
<div class="abs submit">SUBMIT</div>

<div class="abs chat" aria-label="Quick chat"><svg width="20" height="20" viewBox="0 0 24 24" fill="none" stroke="#0a6fc0" stroke-width="1.3"><circle cx="9.5" cy="9.5" r="7.5"/><path d="M8 8a1.6 1.6 0 113 .8c-.7.5-1.5.8-1.5 1.8M9.5 12.8v.4"/><path d="M15 9.5a7 7 0 013.5 11.5L21 22l-4-.8A7 7 0 018 17"/></svg></div>

<div class="abs brand brand-foot"><span class="brand-dot"></span>BRACKWELL EXTERIORS</div>
<div class="abs foot-nav"><span>HOME</span><span>ABOUT US</span><span>SERVICES</span><span>MEET THE TEAM</span><span>CONTACT US</span></div>

<div class="abs fcol" style="left:92px;width:120px">
  <svg width="16" height="28" viewBox="0 0 16 28" fill="none" stroke="#fff" stroke-width="1"><rect x=".5" y=".5" width="15" height="27" rx="2"/><path d="M.5 4h15M.5 23h15"/><circle cx="8" cy="25.5" r=".8"/></svg>
  <h4>PHONE</h4><p>+1 780-555-0184</p>
</div>
<div class="abs fcol" style="left:270px;width:160px">
  <svg width="20" height="28" viewBox="0 0 20 28" fill="none" stroke="#fff" stroke-width="1"><path d="M10 .5a9.5 9.5 0 00-9.5 9.5C.5 17 10 27 10 27s9.5-10 9.5-17A9.5 9.5 0 0010 .5z"/><circle cx="10" cy="10" r="3"/></svg>
  <h4>BRACKWELL EXTERIORS</h4><p>48210 Harlow Rd 118 #305, Elmford<br>Park, AB T9C 2M4, Canada</p>
</div>
<div class="abs fcol" style="left:485px;width:120px">
  <svg width="30" height="24" viewBox="0 0 30 24" fill="none" stroke="#fff" stroke-width="1"><rect x=".5" y="2.5" width="29" height="21"/><path d="M.5 2.5L15 15 29.5 2.5M.5 23.5l11-11M29.5 23.5l-11-11"/></svg>
  <h4>EMAIL</h4><p>hello@brackwellexteriors.ca</p>
</div>

<div class="abs bottom"></div>
<p class="abs copy">Copyright © 2020&nbsp; BRACKWELL EXTERIORS. All Rights Reserved.</p>
<span class="abs social" style="left:524px" aria-label="Social profile"></span>
<span class="abs social" style="left:547px" aria-label="Social profile"></span>
<span class="abs social" style="left:570px" aria-label="Social profile"></span>
<span class="abs social" style="left:593px" aria-label="Social profile"></span>

</body>
</html>
```